Business Card Design Project

Business Card
We are rebranding with a new logo
Industry/Entity Type
Business
Contact Information for Business Card
Dennis Morvale +61 487215963 dennis@quorv.com.au P.O. Box 872 Fernlow QLD 4309
Requirements
Must have
- Logo

```html
<!DOCTYPE html>
<html lang="en">
<head>
<meta charset="utf-8">
<title>Quorv International – Business Card</title>
<link rel="stylesheet" href="https://fonts.googleapis.com/css2?family=Lato:wght@400;700&display=swap">
<style>
  :root {
    --backdrop: #3a3a3c;
    --card-black: #050505;
    --ink-white: #ffffff;
    --brand-orange: #f08a1c;
    --brand-blue: #1e9ad6;
    --glow-orange: #a9541c;
    --glow-teal: #0f5a4e;
    --glow-navy: #141a3a;
    --glow-purple: #2a1f4a;
  }
  * { margin: 0; padding: 0; box-sizing: border-box; }
  html, body {
    width: 1200px;
    height: 926px;
    overflow: hidden;
    background: var(--backdrop);
  }
  .canvas {
    position: relative;
    width: 1200px;
    height: 926px;
    display: flex;
    align-items: center;
    justify-content: center;
  }
  .business-card {
    position: relative;
    width: 980px;
    height: 560px;
    background: var(--card-black);
    overflow: hidden;
    font-family: 'Lato', sans-serif;
    color: var(--ink-white);
    box-shadow: 0 20px 50px rgba(0,0,0,0.45);
  }
  .color-field {
    position: absolute;
    inset: 0;
    width: 100%;
    height: 100%;
  }
  .brand {
    position: absolute;
    left: 70px;
    top: 250px;
    display: flex;
    align-items: center;
    gap: 14px;
  }
  .brand-dot {
    width: 26px;
    height: 26px;
    border-radius: 50%;
    background: var(--brand-blue);
  }
  .brand-name {
    font-weight: 700;
    font-size: 26px;
    letter-spacing: 3px;
    color: var(--brand-blue);
    text-transform: uppercase;
    line-height: 1.2;
  }
  .contact {
    position: absolute;
    left: 540px;
    top: 215px;
  }
  .contact-name {
    font-weight: 700;
    font-size: 36px;
    letter-spacing: 0.5px;
    text-transform: uppercase;
  }
  .rule {
    width: 28px;
    height: 2px;
    background: var(--ink-white);
    margin: 14px 0 12px;
  }
  .contact-line {
    font-size: 22px;
    line-height: 1.4;
  }
  .address {
    font-size: 22px;
  }
</style>
</head>
<body>
<main class="canvas">
  <section class="business-card">
    <svg class="color-field" viewBox="0 0 980 560" preserveAspectRatio="none" role="img" aria-label="Abstract streaked light gradient in orange, teal and violet">
      <defs>
        <linearGradient id="glow" x1="0" y1="0" x2="0.35" y2="1">
          <stop offset="0" stop-color="var(--glow-orange)"/>
          <stop offset="0.3" stop-color="#3d3020"/>
          <stop offset="0.5" stop-color="var(--glow-teal)"/>
          <stop offset="0.75" stop-color="var(--glow-navy)"/>
          <stop offset="1" stop-color="var(--glow-purple)"/>
        </linearGradient>
      </defs>
      <polygon points="460,0 980,0 980,560 250,560" fill="url(#glow)"/>
    </svg>

    <div class="brand">
      <span class="brand-dot"></span>
      <span class="brand-name">Quorv<br>International</span>
    </div>

    <div class="contact">
      <h1 class="contact-name">Dennis Morvale</h1>
      <div class="rule"></div>
      <p class="contact-line">T. +61 487215963</p>
      <p class="contact-line">E. dennis@quorv.com.au</p>
      <div class="rule"></div>
      <p class="address">P.O. Box 872 Fernlow QLD 4309</p>
    </div>
  </section>
</main>
</body>
</html>
```